Company web site

Looking for a full responsive(mobile friendly) wordpress implementation

Some material is in the website -- brelvanto.wordpress.com

But looking for a template more consistent with the logo design, and more future looking.

Target Market(s)

Enterprise Clients

Industry/Entity Type

It Company

Font styles to use
Sans Serif

Colors
33a6d7
0255a3
0455a3
cfdeed
85abd2
3176b5

Requirements
Must have
• about, contact information, partner page, success stories, customer testimonials. links to social presence.
• pricing information

```html
<!DOCTYPE html>
<html lang="en">
<head>
<meta charset="utf-8">
<title>Brelvanto — Integrated Solutions for the IoT Industry</title>
<link href="https://fonts.googleapis.com/css2?family=Jost:wght@400;500;600;700&family=PT+Sans:wght@400;700&display=swap" rel="stylesheet">
<style>
:root{
  --sky:#33a6d7;
  --brand:#0455a3;
  --brand-deep:#0255a3;
  --mist:#cfdeed;
  --soft:#85abd2;
  --mid:#3176b5;
  --ink:#1d2733;
  --text:#5a6470;
  --paper:#ffffff;
  --panel:#eef2f7;
  --line:#d9e1ea;
}
*{box-sizing:border-box;margin:0;padding:0}
html,body{width:1200px;height:4100px;overflow:hidden}
body{font-family:"PT Sans",Arial,sans-serif;color:var(--text);background:var(--paper);position:relative}
.head{font-family:"Jost","Futura",sans-serif;color:var(--brand);font-weight:600}
section,header,footer{position:absolute;left:0;width:1200px}
.center{text-align:center}

/* top bar */
.topbar{top:0;height:50px;border-bottom:1px solid var(--line);font-size:14px;color:var(--text)}
.topbar .support{position:absolute;left:77px;top:15px;display:flex;align-items:center;gap:8px}
.topbar .account{position:absolute;left:855px;top:15px;display:flex;align-items:center;gap:8px}
.topbar .social{position:absolute;left:985px;top:14px;display:flex;gap:18px}
.topbar .social span{width:18px;height:18px;border-radius:3px;background:var(--soft)}

/* nav */
.nav{top:50px;height:110px;background:var(--paper);box-shadow:0 2px 6px rgba(0,0,0,.06);z-index:2}
.brand{position:absolute;left:77px;top:30px;display:flex;align-items:center;gap:10px;font-family:"Jost",sans-serif;font-weight:600;font-size:24px;color:var(--brand)}
.brand i{width:34px;height:34px;border-radius:50%;background:var(--sky);display:block}
.nav ul{position:absolute;right:77px;top:46px;display:flex;gap:34px;list-style:none;font-size:15px;color:var(--brand);letter-spacing:.5px}
.nav li.active{color:var(--sky);border-bottom:2px solid var(--sky);padding-bottom:4px}

/* hero */
.hero{top:160px;height:400px;background:linear-gradient(90deg,#e7ebef 0%,#f3f4f6 60%,#e9ecef 100%)}
.hero .art{position:absolute;left:600px;top:20px;width:560px;height:380px;background:radial-gradient(circle at 55% 45%,#cfe0f1 0%,#e3ebf3 55%,rgba(233,236,239,0) 75%)}
.hero h2{position:absolute;left:77px;top:118px;font-size:33px;color:var(--brand)}
.hero h1{position:absolute;left:77px;top:158px;font-size:66px;line-height:1;font-weight:600;color:var(--brand)}
.hero p{position:absolute;left:77px;top:240px;width:480px;font-size:17px;line-height:1.4;color:var(--text)}
.btn{display:inline-block;font-family:"PT Sans",sans-serif;font-size:17px;letter-spacing:.5px;text-align:center}
.hero .btn{position:absolute;left:77px;top:318px;width:240px;height:52px;line-height:52px;background:var(--brand);color:#fff;border-radius:3px}

/* domain search */
.domain{top:560px;height:300px;background:var(--brand);color:#fff;overflow:hidden}
.domain h2{position:absolute;top:50px;width:100%;font-size:35px;color:#fff;font-weight:500}
.domain .sub{position:absolute;top:105px;width:100%;font-size:14px;color:#dce8f5}
.domain .field{position:absolute;left:213px;top:155px;width:771px;height:52px;background:#fff;border-radius:3px}
.domain .field span{position:absolute;right:6px;top:6px;width:200px;height:40px;line-height:40px;background:var(--brand);color:#fff;font-size:17px;text-align:center}
.domain .prices{position:absolute;left:320px;top:225px;display:flex;gap:56px;font-size:15px;color:#e6eef8}
.domain svg{position:absolute;left:980px;top:90px}

/* about */
.about{top:860px;height:252px}
.about h2{position:absolute;top:50px;width:100%;font-size:38px}
.about p{position:absolute;width:100%;font-size:15px;line-height:1.55}

/* plans */
.plans{top:1112px;height:678px;background:#e8eef5}
.plans h2{position:absolute;top:48px;width:100%;font-size:38px}
.plans .sub{position:absolute;top:106px;width:100%;font-size:15px}
.card{position:absolute;background:#fff;border-radius:4px;box-shadow:0 2px 8px rgba(4,85,163,.08);overflow:hidden}
.card h3{font-family:"Jost",sans-serif;font-weight:500;font-size:28px;color:var(--ink);text-align:center;margin-top:42px}
.card .icon{display:block;margin:22px auto 0}
.card hr{border:0;border-top:1px solid var(--line);margin:16px 28px 14px}
.card ul{list-style:none;padding-left:60px;font-size:14px;line-height:27px}
.card li::before{content:"";display:inline-block;width:6px;height:6px;border-radius:50%;background:#4d5863;margin-right:14px;vertical-align:middle}
.card .price{font-family:"Jost",sans-serif;font-size:32px;color:var(--brand);text-align:center;margin-top:14px}
.card .price small{font-family:"PT Sans",sans-serif;font-size:12px;color:var(--text)}
.card .order{position:absolute;left:50%;transform:translateX(-50%);bottom:40px;width:240px;height:50px;line-height:48px;border:1px solid var(--line);border-radius:4px;color:var(--brand);text-align:center;font-size:17px}
.card.featured .order{background:var(--brand);color:#fff;border-color:var(--brand)}
.ribbon{position:absolute;right:-30px;top:22px;width:130px;height:30px;line-height:30px;background:var(--sky);color:#fff;font-size:12px;text-align:center;transform:rotate(45deg)}

/* features */
.features{top:1790px;height:662px}
.features .screen{position:absolute;left:0;top:60px;width:506px;height:555px;background:linear-gradient(180deg,#2a2f36 0%,#3a4048 70%,#d9dde2 71%,#eef0f2 100%);border-radius:0 10px 10px 0}
.features h2{position:absolute;left:560px;top:70px;font-size:36px;line-height:1.2}
.features p{position:absolute;left:560px;top:170px;width:560px;font-size:16px;line-height:1.4}
.features h3{position:absolute;left:560px;top:262px;font-size:36px}
.features .flow{position:absolute;left:560px;top:300px}
.step{font-family:"Jost",sans-serif;font-weight:600;font-size:28px;fill:var(--ink)}

/* testimonial */
.testimonial{top:2452px;height:440px;background:linear-gradient(180deg,#eef1f5,#e6ebf1)}
.testimonial h2{position:absolute;top:50px;width:100%;font-size:38px}
.testimonial blockquote{position:absolute;left:230px;top:110px;width:740px;font-size:16px;line-height:1.5;text-align:center}
.avatar{position:absolute;left:556px;top:200px;width:88px;height:88px;border-radius:50%;background:#9bb3c9;border:4px solid var(--brand)}
.testimonial .name{position:absolute;top:294px;width:100%;font-family:"Jost",sans-serif;font-size:24px;color:var(--brand)}
.testimonial .role{position:absolute;top:326px;width:100%;font-size:13px}
.dots{position:absolute;top:368px;left:0;width:100%;display:flex;justify-content:center;gap:8px}
.dots span{width:11px;height:11px;border-radius:50%;background:var(--brand)}
.dots span.on{background:var(--soft);box-shadow:0 0 0 3px var(--mist)}

/* offers */
.offers{top:2892px;height:178px;background:linear-gradient(90deg,var(--brand) 0%,var(--mid) 100%);color:#fff}
.offers h2{position:absolute;left:77px;top:50px;font-size:38px;color:#fff}
.offers p{position:absolute;left:77px;top:100px;font-size:18px;color:#e3ecf7}
.offers .btn{position:absolute;left:883px;top:60px;width:238px;height:54px;line-height:54px;background:#fff;color:var(--brand);border-radius:3px}

/* blog */
.blog{top:3070px;height:456px}
.blog h2{position:absolute;top:48px;width:100%;font-size:38px}
.post{position:absolute;top:108px;width:370px}
.post .thumb{width:370px;height:162px}
.post h3{font-family:"PT Sans",sans-serif;font-weight:700;font-size:17px;color:var(--ink);margin-top:18px}
.post p{font-size:14px;line-height:1.5;margin-top:6px;width:330px}
.post a{display:inline-block;margin-top:12px;font-weight:700;color:var(--brand);border-bottom:1px solid var(--brand);font-size:16px}

/* partners */
.partners{top:3526px;height:254px;background:#e4ebf4}
.partners h2{position:absolute;top:48px;width:100%;font-size:38px}
.partners .row{position:absolute;left:77px;top:98px;display:flex;gap:9px}
.partners .badge{width:166px;height:100px;background:#fff;border:1px solid var(--line);display:flex;align-items:center;justify-content:center}
.partners .badge i{display:block;width:110px;height:32px;border-radius:4px;background:#d3d9e0}

/* footer */
.footer{top:3780px;height:260px;background:var(--brand);color:#fff;font-size:14px}
.footer h4{font-family:"Jost",sans-serif;font-weight:600;font-size:18px;margin-bottom:14px}
.col{position:absolute;top:40px}
.contact li{list-style:none;display:flex;gap:8px;margin-bottom:12px;line-height:1.4}
.links{display:flex;gap:40px}
.links ul{list-style:none;line-height:1.85}
.links li::before{content:"•";margin-right:8px}
.news .input{width:250px;height:40px;background:var(--mid);border-radius:2px;padding:11px 12px;font-size:12px;color:#cfe0f1;margin-top:10px}
.news .sub{margin-top:14px;width:190px;height:40px;line-height:40px;background:#fff;color:var(--brand);text-align:center;font-size:17px}
.fbrand{position:absolute;left:970px;top:60px;width:150px;text-align:center;font-family:"Jost",sans-serif;font-weight:600;font-size:20px}
.fbrand i{display:block;width:56px;height:56px;border-radius:50%;background:var(--soft);margin:0 auto 10px}
.fsocial{display:flex;gap:8px;justify-content:center;margin-top:12px}
.fsocial span{width:30px;height:30px;border:1px solid var(--soft)}
.copy{position:absolute;top:4040px;left:0;width:1200px;height:60px;line-height:60px;text-align:center;font-size:13px;color:var(--text)}
.copy b{color:var(--brand);font-weight:400}
</style>
</head>
<body>

<header class="topbar">
  <div class="support">
    <svg width="16" height="16" viewBox="0 0 16 16"><circle cx="8" cy="8" r="7" fill="none" stroke="#5a6470" stroke-width="1.4"/><path d="M8 4v4l3 2" stroke="#5a6470" stroke-width="1.4" fill="none"/></svg>
    24/7 Support : +1-(555) 014-2290
  </div>
  <div class="account">
    <svg width="16" height="16" viewBox="0 0 16 16"><circle cx="8" cy="5" r="3" fill="none" stroke="#5a6470" stroke-width="1.4"/><path d="M2 15c1-4 11-4 12 0" fill="none" stroke="#5a6470" stroke-width="1.4"/></svg>
    My Account
  </div>
  <div class="social"><span></span><span></span><span></span><span></span></div>
</header>

<nav class="nav">
  <div class="brand"><i></i>Brelvanto</div>
  <ul>
    <li class="active">HOME</li><li>ABOUT US</li><li>PLATFORM</li><li>PARTNERS</li><li>PRICING</li><li>BLOG</li><li>CONTACT US</li>
  </ul>
</nav>

<section class="hero">
  <div class="art" role="img" aria-label="Illustration of hands holding a tablet connected by lines to icons of smart devices"></div>
  <h2 class="head">Integrated Solutions for the</h2>
  <h1 class="head">IoT INDUSTRY</h1>
  <p>Brelvanto is company which provides specialized offerings in IoT domain. Based in the heart of the Silicon Valley, California.</p>
  <span class="btn">GET STARTED NOW</span>
</section>

<section class="domain">
  <h2 class="head center">Search Your Domain Name</h2>
  <div class="sub center">Free Email accounts and privacy protection comes in your way</div>
  <div class="field"><span>SEARCH DOMAIN</span></div>
  <div class="prices"><span>.com $7.45</span><span>.net $7.50</span><span>.org $5.50</span><span>.us $8.80</span><span>.biz $8.35</span></div>
  <svg width="260" height="260" viewBox="0 0 260 260" opacity=".18"><circle cx="110" cy="110" r="80" fill="none" stroke="#85abd2" stroke-width="22"/><path d="M170 170l70 70" stroke="#85abd2" stroke-width="30" stroke-linecap="round"/></svg>
</section>

<section class="about">
  <h2 class="head center">About Us</h2>
  <p class="center" style="top:115px">Founded in 2016 by industry veterans, Brelvanto is geared to provide integrated solutions for the IoT industry</p>
  <p class="center" style="top:150px;left:200px;width:800px">With a off-shore development center in Eastern Europe, Brelvanto is positioned to provided extensive development capabilities to our customers.</p>
</section>

<section class="plans">
  <h2 class="head center">Choose Your Plan</h2>
  <div class="sub center">Pay for what you actully use. No hidden charge!</div>

  <div class="card" style="left:77px;top:184px;width:333px;height:454px">
    <h3>Standard</h3>
    <svg class="icon" width="46" height="40" viewBox="0 0 46 40"><rect x="3" y="3" width="40" height="26" fill="none" stroke="#1d2733" stroke-width="2.5"/><path d="M17 37h12M23 29v8" stroke="#1d2733" stroke-width="2.5"/><path d="M23 8v14M18 13l5-5 5 5" stroke="#1d2733" stroke-width="2.5" fill="none"/></svg>
    <hr>
    <ul><li>Lorem Ipsum is simply dummy text</li><li>Lorem Ipsum is simply dummy text</li><li>Lorem Ipsum is simply dummy text</li><li>Lorem Ipsum is simply dummy text</li><li>Lorem Ipsum is simply dummy text</li></ul>
    <div class="price">$8.30 <small>/ month</small></div>
    <div class="order">ORDER NOW</div>
  </div>

  <div class="card featured" style="left:429px;top:151px;width:342px;height:475px">
    <div class="ribbon">POPULAR</div>
    <h3 style="margin-top:28px">Business</h3>
    <svg class="icon" width="60" height="40" viewBox="0 0 60 40"><path d="M4 14l12-8 10 6 10-6 20 10-14 16-10-6-8 4L4 24z" fill="none" stroke="#1d2733" stroke-width="2.5" stroke-linejoin="round"/><path d="M26 12l10 10" stroke="#1d2733" stroke-width="2.5"/></svg>
    <hr>
    <ul><li>Lorem Ipsum is simply dummy text</li><li>Lorem Ipsum is simply dummy text</li><li>Lorem Ipsum is simply dummy text</li><li>Lorem Ipsum is simply dummy text</li><li>Lorem Ipsum is simply dummy text</li></ul>
    <div class="price">$8.30 <small>/ month</small></div>
    <div class="order">ORDER NOW</div>
  </div>

  <div class="card" style="left:790px;top:184px;width:333px;height:454px">
    <h3>Professional</h3>
    <svg class="icon" width="40" height="44" viewBox="0 0 40 44"><circle cx="20" cy="10" r="7" fill="none" stroke="#1d2733" stroke-width="2.5"/><path d="M6 42V28c0-6 28-6 28 0v14M20 22l-3 6 3 12 3-12z" fill="none" stroke="#1d2733" stroke-width="2.5" stroke-linejoin="round"/></svg>
    <hr>
    <ul><li>Lorem Ipsum is simply dummy text</li><li>Lorem Ipsum is simply dummy text</li><li>Lorem Ipsum is simply dummy text</li><li>Lorem Ipsum is simply dummy text</li><li>Lorem Ipsum is simply dummy text</li></ul>
    <div class="price">$8.30 <small>/ month</small></div>
    <div class="order">ORDER NOW</div>
  </div>
</section>

<section class="features">
  <div class="screen" role="img" aria-label="Desktop monitor showing a dashboard with a map of connected devices and a line chart"></div>
  <h2 class="head">Focus on your product.<br>We manage the integrations.</h2>
  <p>With Brelvanto you pick-and-choose the features your customers want, based on our modular architecture. And get all the tools you need to operate your IoT business.</p>
  <h3 class="head">Connected Product</h3>
  <svg class="flow" width="600" height="320" viewBox="0 0 600 320">
    <path d="M0 130 C120 110 200 90 300 110 S500 150 600 150" fill="none" stroke="#cfdeed" stroke-width="2" stroke-dasharray="6 6"/>
    <circle cx="96" cy="100" r="70" fill="#fff" stroke="#85abd2" stroke-width="6"/>
    <circle cx="96" cy="100" r="58" fill="#fff"/>
    <path d="M96 70a16 16 0 0 1 10 29v8H86v-8a16 16 0 0 1 10-29zM88 114h16" fill="none" stroke="#0455a3" stroke-width="3"/>
    <path d="M80 84l-8-8M112 84l8-8M96 64v-10" stroke="#33a6d7" stroke-width="3"/>
    <rect x="76" y="156" width="40" height="40" fill="#0455a3"/>
    <path d="M96 166v20M86 176h20" stroke="#fff" stroke-width="3"/>
    <text class="step" x="96" y="236" text-anchor="middle">Learn</text>
    <circle cx="295" cy="92" r="62" fill="#fff" stroke="#cfdeed" stroke-width="6"/>
    <circle cx="295" cy="92" r="52" fill="#0455a3"/>
    <circle cx="280" cy="78" r="7" fill="none" stroke="#fff" stroke-width="3"/><circle cx="310" cy="92" r="7" fill="none" stroke="#fff" stroke-width="3"/><circle cx="280" cy="108" r="7" fill="none" stroke="#fff" stroke-width="3"/>
    <path d="M286 82l18 7M286 104l18-8" stroke="#fff" stroke-width="3"/>
    <text class="step" x="295" y="186" text-anchor="middle">Connect</text>
    <circle cx="487" cy="128" r="62" fill="#fff" stroke="#cfdeed" stroke-width="6"/>
    <circle cx="487" cy="128" r="52" fill="#0455a3"/>
    <rect x="463" y="112" width="22" height="22" rx="3" fill="none" stroke="#fff" stroke-width="3"/><rect x="489" y="122" width="22" height="22" rx="3" fill="none" stroke="#fff" stroke-width="3"/>
    <text class="step" x="487" y="224" text-anchor="middle">Integrate</text>
  </svg>
</section>

<section class="testimonial">
  <h2 class="head center">Testimonial</h2>
  <blockquote>"Lorem Ipsum is simply dummy text of the printing and typesetting industry. Lorem Ipsum has been the industry's standard dummy text ever since the 1500s, when an unknown printer took a galley of type and scrambled it to make a type specimen book."</blockquote>
  <div class="avatar" role="img" aria-label="Portrait photo of the client"></div>
  <div class="name center">Daniel Reeve</div>
  <div class="role center">DR Reeve Law, PC</div>
  <div class="dots"><span></span><span class="on"></span><span></span></div>
</section>

<section class="offers">
  <h2 class="head">To Get Special Offers From Us</h2>
  <p>Lorem Ipsum is simply dummy text of the printing and typesetting industry.</p>
  <span class="btn">GET STARTED NOW</span>
</section>

<section class="blog">
  <h2 class="head center">Our Blogs</h2>
  <article class="post" style="left:210px">
    <div class="thumb" role="img" aria-label="Photo of a city skyline at night with glowing data lines" style="background:linear-gradient(180deg,#4fb0e6 0%,#1f5fa8 55%,#0c2347 100%)"></div>
    <h3>Lorem Ipsume is dummy text</h3>
    <p>Lorem Ipsum is simply dummy text of the printing and typesetting industry.</p>
    <a>Read More</a>
  </article>
  <article class="post" style="left:615px">
    <div class="thumb" role="img" aria-label="Photo of a businessman using a tablet" style="background:linear-gradient(120deg,#2c3f55 0%,#7d8fa3 55%,#dfe5ea 100%)"></div>
    <h3>Lorem Ipsume is dummy text</h3>
    <p>Lorem Ipsum is simply dummy text of the printing and typesetting industry.</p>
    <a>Read More</a>
  </article>
</section>

<section class="partners">
  <h2 class="head center">Our Partner</h2>
  <div class="row">
    <div class="badge"><i></i></div><div class="badge"><i></i></div><div class="badge"><i></i></div>
    <div class="badge"><i></i></div><div class="badge"><i></i></div><div class="badge"><i></i></div>
  </div>
</section>

<footer class="footer">
  <div class="col contact" style="left:77px">
    <h4>Contact Us</h4>
    <ul>
      <li><svg width="14" height="18" viewBox="0 0 14 18"><path d="M7 1a6 6 0 0 1 6 6c0 4-6 10-6 10S1 11 1 7a6 6 0 0 1 6-6z" fill="#fff"/><circle cx="7" cy="7" r="2" fill="#0455a3"/></svg><span>418 Arden Way<br>Palo Mesa, CA 95190</span></li>
      <li><svg width="14" height="14" viewBox="0 0 14 14"><path d="M3 1l3 3-2 2c1 2 2 3 4 4l2-2 3 3-2 2C6 13 1 8 1 3z" fill="#fff"/></svg>+1-(555) 014-2290</li>
      <li><svg width="16" height="12" viewBox="0 0 16 12"><rect width="16" height="12" fill="#fff"/><path d="M0 0l8 6 8-6" stroke="#0455a3" fill="none"/></svg>info@brelvanto.com</li>
    </ul>
  </div>
  <div class="col" style="left:345px">
    <h4>Quick Links</h4>
    <div class="links">
      <ul><li><b>Home</b></li><li>About</li><li>Platform</li><li>Testimonial</li><li>Success Stories</li></ul>
      <ul><li>Privacy Policy</li><li>Support</li><li>Blogs</li><li>Partners</li><li>Contact Us</li></ul>
    </div>
  </div>
  <div class="col news" style="left:608px">
    <h4>Newsletter</h4>
    <div>Get Latest News &amp; Updates About us.</div>
    <div class="input">E-Mail Address</div>
    <div class="sub">SUBSCRIBE</div>
  </div>
  <div class="fbrand"><i></i>Brelvanto
    <div class="fsocial"><span style="background:#fff"></span><span></span><span></span><span></span></div>
  </div>
</footer>
<div class="copy">© <b>Brelvanto</b> - 2017, All Rights Reserved.</div>

</body>
</html>
```